Innovative coffee bean bag design for roasters

We need a design which can be printed on a coffee bean bag but which could also work on a sticker of similar size. We're after quirky, geeky, playful and innovative. Something that will stand out and communicate the character of our business. It should be eye catching and draw the customer in for a closer look.
Thematically, think organic and earthy.
It needs an element which can be changed for different coffee origins and roast profiles, so the main design will remain the same but with a feature which changes to help the customer know what they're looking at and will make them smile.
Approximate dimensions we need are 15cm by 12cm, with the 15cm being the vertical height of the bag image. (The image will be viewed in portrait). This is the main print area - however, if you have a great idea for a full bag image (approximately 23cm by 13cm), feel free to submit this too, we're interested in all ideas.
There is an image attached of a white partially see-through bag which we are considering using, so keep this in mind when designing.
We will need our logo including - see attached image.
Finally, we need space for the information about the coffee, such as origin, roast profile, flavour notes - see attached image for an example of the information (not necessarily a stylistic indicator). Please suggest fonts etc.

Target Market(s)

coffee roasters

Requirements
Must have
• Must say under the logo coffee roasters( Copper Kettle Organic Coffee Roasters )
Nice to have
• Unique symbol, shapes, scientific.

```html
<!DOCTYPE html>
<html lang="en">
<head>
<meta charset="utf-8">
<title>Copper Kettle Organic Coffee Roasters – Coffee Roast Label</title>
<link href="https://fonts.googleapis.com/css2?family=Lexend:wght@400;500;600;700&family=Dancing+Script:wght@500&display=swap" rel="stylesheet">
<style>
  :root {
    --backdrop: #9aadbd;
    --label-black: #111111;
    --panel-white: #ffffff;
    --ink: #1a1a1a;
    --script-blue: #2f5f9a;
    --art-cream: #d9cfb8;
    --art-rust: #b2452a;
    --art-blue: #4f6f9e;
  }
  * { box-sizing: border-box; margin: 0; padding: 0; }
  html, body { width: 1200px; height: 1200px; overflow: hidden; }
  body { background: var(--backdrop); position: relative; font-family: "Lexend", sans-serif; }

  .label { position: absolute; left: 210px; top: 100px; width: 780px; height: 1000px; }
  .label-shape { position: absolute; inset: 0; }

  .brand { position: absolute; top: 62px; left: 0; width: 100%; text-align: center;
    color: #fff; font-family: "Lexend", sans-serif; font-weight: 500; }
  .brand-name { font-size: 46px; letter-spacing: 3px; line-height: 1.1; }
  .brand-sub { font-size: 24px; letter-spacing: 2px; margin-top: 40px; }

  .illustration { position: absolute; left: 80px; top: 245px; width: 620px; height: 400px;
    border-radius: 30px 30px 0 0;
    background: radial-gradient(ellipse at 45% 55%, var(--art-cream) 0%, #a99f88 35%, rgba(178,69,42,0.55) 55%, rgba(79,111,158,0.25) 70%, var(--label-black) 85%); }

  .info-panel { position: absolute; left: 33px; top: 617px; width: 701px; height: 368px;
    background: var(--panel-white); border: 3px solid var(--panel-white);
    outline: 2px solid var(--ink); outline-offset: -14px; color: var(--ink); }
  .roast-title { position: absolute; top: 42px; width: 100%; text-align: center;
    font-weight: 600; font-size: 50px; letter-spacing: 4px; }
  .rule { position: absolute; left: 38px; right: 38px; height: 2px; background: var(--ink); }
  .rule-1 { top: 108px; } .rule-2 { top: 168px; } .rule-3 { top: 240px; }
  .flavour-notes { position: absolute; top: 132px; width: 100%; text-align: center;
    font-weight: 600; font-size: 24px; letter-spacing: 4px; }
  .roast-profile { position: absolute; top: 174px; width: 100%; text-align: center;
    font-family: "Dancing Script", cursive; font-size: 58px; color: var(--script-blue); }

  .facts { position: absolute; top: 252px; left: 38px; right: 38px; height: 90px;
    display: flex; align-items: center; }
  .fact { text-align: center; text-transform: uppercase; }
  .fact-origin { width: 140px; text-align: left; }
  .fact-form { width: 170px; }
  .fact-weight { flex: 1; text-align: right; }
  .divider { width: 2px; height: 74px; background: var(--ink); }
  .fact-label { font-weight: 600; font-size: 23px; letter-spacing: 3px; line-height: 1.3; }
  .fact-value { font-weight: 600; font-size: 40px; letter-spacing: 3px; line-height: 1.1; }
</style>
</head>
<body>
  <div class="label">
    <svg class="label-shape" viewBox="0 0 780 1000" width="780" height="1000" aria-hidden="true">
      <path d="M0 160 L60 160 C110 40 250 10 390 10 C530 10 670 40 720 160 L780 160 L780 1000 L0 1000 Z" fill="var(--label-black)"/>
    </svg>

    <div class="brand">
      <div class="brand-name">Copper Kettle</div>
      <div class="brand-sub">Organic Coffee Roasters</div>
    </div>

    <div class="illustration" role="img" aria-label="Illustration of an astronaut in a cream spacesuit with rust harness holding a coffee cup among stars and a small red planet"></div>

    <div class="info-panel">
      <div class="roast-title">COFFEE ROAST</div>
      <div class="rule rule-1"></div>
      <div class="flavour-notes">CITRUS FRUIT · FLORAL</div>
      <div class="rule rule-2"></div>
      <div class="roast-profile">Premium Roast</div>
      <div class="rule rule-3"></div>
      <div class="facts">
        <div class="fact fact-origin">
          <div class="fact-label">Origin</div>
          <div class="fact-value">Perú</div>
        </div>
        <div class="divider"></div>
        <div class="fact fact-form">
          <div class="fact-label">Whole<br>Bean</div>
        </div>
        <div class="divider"></div>
        <div class="fact fact-weight">
          <div class="fact-label">Net. Weight</div>
          <div class="fact-value">12oz (340g)</div>
        </div>
      </div>
    </div>
  </div>
</body>
</html>
```